Business Card for Health Food Store

I need a business card for a health food store that includes the following information.

=========
FRONT
=========

***White background***

Bright Harvest (logo)
Supplements - Health Foods - Remedies

2214 Alder Rd.
Maple Grove, CA 94510
(corner of Ferris Ln.)

707-482-3196

BrightHarvest.co
BrightHarvestGoods@mailbox-example.com

On the right side of the front of the card, use a circle type seal with 25 large in the middle. Put the dates below it.
"Celebrating 25 Years"
1997 - 2022

*DO NOT USE A PERSON'S NAME ON THE CARD*

==========
BACK
==========

***Green background***

Full logo in white along with the social logos and handles.

FB Logo / BrightHarvestShop
IG Logo / BrightHarvestShop
Twitter Logo / VisitBrightHarvest

When done I'll need the file in PSD and AI.

Target Market(s)

Surrounding local community

Industry/Entity Type

Retail Health Food Store

Contact Information for Business Card

See brief

Requirements
Must have
• Must be double-sided

```html
<!DOCTYPE html>
<html lang="en">
<head>
<meta charset="utf-8">
<title>Bright Harvest Business Card</title>
<link rel="stylesheet" href="https://fonts.googleapis.com/css2?family=Arimo:wght@400;700&family=Roboto+Condensed:wght@700&display=swap">
<style>
  :root {
    --backdrop: #2b2b2b;
    --card-dark: #1b1b1b;
    --card-light: #ffffff;
    --leaf-green: #4cbc1c;
    --ink: #111111;
    --paper-text: #f2f2f2;
    --social-blue: #3b5998;
    --social-pink: #d6306f;
  }
  * { margin: 0; padding: 0; box-sizing: border-box; }
  html, body { width: 1200px; height: 1015px; overflow: hidden; }
  body {
    background: radial-gradient(ellipse at center, #3a3a3a 0%, var(--backdrop) 60%, #151515 100%);
    font-family: "Arimo", Arial, sans-serif;
    position: relative;
  }
  .card {
    position: absolute;
    left: 250px;
    width: 700px;
    height: 400px;
    overflow: hidden;
    box-shadow: 0 18px 40px rgba(0,0,0,0.6);
  }
  .card--back { top: 85px; }
  .card--front { top: 530px; }
  .card-art { position: absolute; inset: 0; }
  .brand {
    position: absolute;
    text-align: center;
  }
  .brand-name {
    font-weight: 700;
    color: var(--ink);
    line-height: 1;
    letter-spacing: -0.5px;
    white-space: nowrap;
  }
  .brand-tagline {
    font-family: "Roboto Condensed", "Arial Narrow", sans-serif;
    font-weight: 700;
    color: var(--leaf-green);
    letter-spacing: 1px;
    margin-top: 6px;
    white-space: nowrap;
  }
  .card--back .brand { left: 45px; top: 160px; width: 360px; }
  .card--back .brand-name { font-size: 42px; }
  .card--back .brand-tagline { font-size: 13px; }
  .card--front .brand { left: 410px; top: 145px; width: 300px; }
  .card--front .brand-name { font-size: 36px; }
  .card--front .brand-tagline { font-size: 11px; }

  .anniversary {
    position: absolute;
    left: 500px;
    top: 60px;
    text-align: center;
    font-size: 17px;
    line-height: 1.2;
    color: var(--paper-text);
  }
  .anniversary-years { color: var(--leaf-green); }

  .socials {
    position: absolute;
    left: 500px;
    top: 180px;
    width: 180px;
    text-align: center;
    color: var(--paper-text);
    font-size: 16px;
  }
  .social { margin-bottom: 22px; }
  .social-dot {
    display: block;
    width: 18px;
    height: 18px;
    border-radius: 50%;
    margin: 0 auto 4px;
  }
  .social-dot--fb { background: var(--social-blue); }
  .social-dot--ig { background: var(--social-pink); }

  .address, .contacts {
    position: absolute;
    left: 40px;
    color: var(--paper-text);
  }
  .address {
    top: 70px;
    display: flex;
    gap: 12px;
    font-size: 19px;
    line-height: 1.25;
  }
  .contacts {
    top: 290px;
    font-size: 16px;
    line-height: 1.5;
  }
  .contact-row { display: flex; align-items: center; gap: 10px; white-space: nowrap; }
  .contact-row svg, .address svg { flex: none; }
  .contact-web { color: var(--leaf-green); }
  .contact-web span { color: var(--paper-text); }
</style>
</head>
<body>

<section class="card card--back" aria-label="Card back">
  <svg class="card-art" width="700" height="400" viewBox="0 0 700 400">
    <rect width="700" height="400" fill="var(--card-dark)"/>
    <circle cx="200" cy="190" r="280" fill="var(--card-light)"/>
    <path d="M246 -74 A268 268 0 0 1 334 422" fill="none" stroke="var(--leaf-green)" stroke-width="4"/>
  </svg>
  <div class="brand">
    <div class="brand-name">Bright Harvest</div>
    <div class="brand-tagline">SUPPLEMENTS · HEALTH FOODS · REMEDIES</div>
  </div>
  <div class="anniversary">
    <div>Celebrating 25 Years</div>
    <div class="anniversary-years">1997 - 2022</div>
  </div>
  <div class="socials">
    <div class="social"><span class="social-dot social-dot--fb"></span>/brightharvestfoods</div>
    <div class="social"><span class="social-dot social-dot--ig"></span>/BrightHarvestShop</div>
  </div>
</section>

<section class="card card--front" aria-label="Card front">
  <svg class="card-art" width="700" height="400" viewBox="0 0 700 400">
    <rect width="700" height="400" fill="var(--card-dark)"/>
    <circle cx="565" cy="165" r="212" fill="var(--card-light)"/>
    <path d="M410 35 A202 202 0 0 0 530 364" fill="none" stroke="var(--leaf-green)" stroke-width="4"/>
  </svg>
  <div class="brand">
    <div class="brand-name">Bright Harvest</div>
    <div class="brand-tagline">SUPPLEMENTS · HEALTH FOODS · REMEDIES</div>
  </div>
  <div class="address">
    <svg width="16" height="22" viewBox="0 0 16 22" aria-hidden="true">
      <path d="M8 0C3.6 0 0 3.5 0 7.8 0 13.5 8 22 8 22s8-8.5 8-14.2C16 3.5 12.4 0 8 0z" fill="var(--leaf-green)"/>
      <circle cx="8" cy="8" r="3" fill="var(--card-dark)"/>
    </svg>
    <div>2214 Alder Rd.<br>Maple Grove, CA 94510</div>
  </div>
  <div class="contacts">
    <div class="contact-row">
      <svg width="18" height="18" viewBox="0 0 24 24" aria-hidden="true"><path d="M6.6 10.8a15 15 0 0 0 6.6 6.6l2.2-2.2c.3-.3.7-.4 1-.2 1.1.4 2.300.6 3.600.6.6 0 1 .4 1 1V20c0 .6-.4 1-1 1C10.6 21 3 13.4 3 4c0-.6.4-1 1-1h3.5c.6 0 1 .4 1 1 0 1.3.2 2.5.6 3.600.1.3 0 .7-.2 1z" fill="var(--leaf-green)"/></svg>
      707-482-3196
    </div>
    <div class="contact-row contact-web">
      <svg width="18" height="18" viewBox="0 0 24 24" aria-hidden="true" fill="none" stroke="var(--leaf-green)" stroke-width="2"><circle cx="12" cy="12" r="10"/><ellipse cx="12" cy="12" rx="4" ry="10"/><path d="M2 12h20M4 7h16M4 17h16"/></svg>
      <div>BrightHarvest<span>.com</span></div>
    </div>
    <div class="contact-row">
      <svg width="18" height="14" viewBox="0 0 24 18" aria-hidden="true"><rect width="24" height="18" fill="var(--leaf-green)"/><path d="M0 0l12 10L24 0" fill="none" stroke="var(--card-dark)" stroke-width="2"/></svg>
      BrightHarvestGoods@mailbox-example.com
    </div>
  </div>
</section>

</body>
</html>
```